redesign of my existing custom website into Wordpress based website

I need someone to redesign my current website into something more classy, simplistic, modern and on trend. I would like it set up on Wordpress in a way thats easy for me to make my own additions to blogs/price changes and promotion banners. I will also need a page that is password protected so members can login and have access to all my training videos and resources.
website is www.tidewellmamas.com.au

Target Market(s)

new mums

Industry/Entity Type

Fitness

Coding

Coded - Design and coding required

Number of Pages Required

5+ page

Colors
33a6d7

Requirements
Must have
• chic, modern, stylish and simplistic.
• a call to action above the page fold
• mobile friendly conversion
• a pop up message as soon as someone enters my sight offering my free report
• a members page that is password protected containing 3 youtube videos and 6 pdf attachments as resources
• a home page
• a contact us page
• an about us page
• a blog page
• a store page
Nice to have
• some examples of my peers websites that I like:
• www.norapellwick.com
• https://www.9qlr.com
• https://41bytedgarth.com
Should not have
• anything gimmicky

```html
<!DOCTYPE html>
<html lang="en">
<head>
<meta charset="utf-8">
<title>About Us – Tidewell Mamas</title>
<link href="https://fonts.googleapis.com/css2?family=Lato:wght@400;700&family=Open+Sans:wght@400;600&display=swap" rel="stylesheet">
<style>
  :root {
    --accent: #33a6d7;
    --ink: #2b2b2b;
    --body: #6a6a6a;
    --muted: #555555;
    --rule: #cfcfcf;
    --white: #ffffff;
  }
  * { box-sizing: border-box; margin: 0; padding: 0; }
  html, body { width: 712px; height: 1200px; overflow: hidden; background: var(--white); }
  body { position: relative; font-family: "Open Sans", Arial, sans-serif; color: var(--body); }
  .abs { position: absolute; }

  .top-bar { left: 0; top: 0; width: 712px; height: 2px; background: var(--accent); }

  .site-header { left: 0; top: 2px; width: 712px; height: 52px; }
  .brand { display: flex; align-items: center; gap: 6px; font-family: "Lato", Arial, sans-serif; font-weight: 700; color: var(--ink); white-space: nowrap; }
  .brand-dot { border: 2px solid var(--ink); border-radius: 50%; }
  .header-brand { left: 76px; top: 12px; font-size: 13px; }
  .header-brand .brand-dot { width: 22px; height: 22px; }
  .main-nav a { position: absolute; top: 21px; font-family: "Lato", Arial, sans-serif; font-size: 9.6px; font-weight: 700; color: var(--ink); text-decoration: none; letter-spacing: .2px; white-space: nowrap; }
  .main-nav a.is-current { color: var(--accent); }
  .btn-login { left: 536px; top: 15px; width: 58px; height: 21px; border: 1px solid #bdbdbd; border-radius: 11px; display: flex; align-items: center; justify-content: center; gap: 4px; font-family: "Lato", Arial, sans-serif; font-weight: 700; font-size: 9px; color: var(--ink); }
  .btn-join { left: 597px; top: 15px; width: 56px; height: 21px; border-radius: 11px; background: var(--accent); color: var(--white); font-family: "Lato", Arial, sans-serif; font-weight: 700; font-size: 9px; display: flex; align-items: center; justify-content: center; }

  .hero { left: 0; top: 54px; width: 712px; height: 186px; background: linear-gradient(100deg, #3a3434 0%, #6b5a5c 30%, #b05b83 48%, #4b4545 70%, #2f2b2b 100%); }
  .hero-shade { left: 0; top: 54px; width: 712px; height: 186px; background: rgba(0,0,0,.28); }
  .hero-quote { left: 100px; top: 88px; width: 512px; text-align: center; font-family: "Lato", Arial, sans-serif; font-weight: 700; font-size: 16px; line-height: 25px; color: var(--white); text-transform: uppercase; text-shadow: 0 1px 3px rgba(0,0,0,.5); }
  .hero-author { left: 100px; top: 173px; width: 512px; text-align: center; font-size: 12.5px; color: var(--white); text-shadow: 0 1px 3px rgba(0,0,0,.5); }

  .breadcrumb { left: 58px; top: 258px; font-family: "Lato", Arial, sans-serif; font-size: 9px; color: var(--ink); }
  .breadcrumb .is-current { color: var(--accent); font-weight: 700; }
  .rule { left: 58px; top: 282px; width: 596px; height: 1px; background: var(--rule); }

  .founder-photo { left: 58px; top: 312px; width: 204px; height: 255px; background: linear-gradient(160deg, #9a7f72 0%, #e8c7b9 40%, #c9a5c4 65%, #8cc06a 85%, #5d5a55 100%); box-shadow: 0 0 2px rgba(0,0,0,.35); }

  .story { left: 289px; top: 311px; width: 366px; font-size: 7.3px; line-height: 15.2px; }
  .story p { margin-bottom: 15.2px; }

  .cta-band { left: 0; top: 860px; width: 712px; height: 150px; background: linear-gradient(100deg, #d9d9d9 0%, #e6e2e4 45%, #e9d9e1 55%, #dedede 100%); }
  .cta-title { left: 0; top: 888px; width: 712px; text-align: center; font-family: "Lato", Arial, sans-serif; font-weight: 400; font-size: 17.6px; color: var(--ink); }
  .cta-sub { left: 0; top: 918px; width: 712px; text-align: center; font-family: "Lato", Arial, sans-serif; font-size: 10.8px; color: var(--muted); }
  .btn-cta { left: 300px; top: 948px; width: 112px; height: 25px; border-radius: 13px; background: var(--accent); color: var(--white); font-family: "Lato", Arial, sans-serif; font-weight: 700; font-size: 9.3px; display: flex; align-items: center; justify-content: center; }

  .footer-brand { left: 58px; top: 1068px; font-size: 15px; }
  .footer-brand .brand-dot { width: 28px; height: 28px; }
  .footer-heading { top: 1038px; font-family: "Lato", Arial, sans-serif; font-weight: 400; font-size: 11.5px; color: var(--ink); }
  .quick-links { left: 226px; top: 1061px; list-style: none; font-size: 7.4px; line-height: 13.6px; }
  .quick-links a { color: var(--muted); text-decoration: none; }
  .subscribe-text { left: 330px; top: 1061px; width: 160px; font-size: 7.2px; line-height: 13.6px; color: var(--muted); }
  .btn-subscribe { left: 331px; top: 1112px; width: 71px; height: 22px; border-radius: 11px; background: var(--accent); color: var(--white); font-family: "Lato", Arial, sans-serif; font-weight: 700; font-size: 8.4px; display: flex; align-items: center; justify-content: center; }
  .social { left: 531px; font-size: 7.2px; color: var(--muted); display: flex; align-items: center; gap: 12px; }
  .social-mark { width: 18px; height: 18px; background: #8a8a8a; border-radius: 2px; }

  .footer-rule { left: 58px; top: 1158px; width: 596px; height: 1px; background: var(--rule); }
  .copyright { left: 0; top: 1172px; width: 712px; text-align: center; font-size: 7.2px; color: var(--muted); }
</style>
</head>
<body>
  <div class="abs top-bar"></div>

  <header class="abs site-header">
    <div class="abs brand header-brand"><span class="brand-dot"></span>Tidewell Mamas</div>
    <nav class="main-nav">
      <a style="left:213px">HOME</a>
      <a class="is-current" style="left:262px">ABOUT US</a>
      <a style="left:326px">PROGRAM</a>
      <a style="left:391px">BLOG</a>
      <a style="left:436px">FAQ</a>
      <a style="left:476px">CONTACT</a>
    </nav>
    <div class="abs btn-login">
      <svg width="7" height="8" viewBox="0 0 7 8" aria-hidden="true"><rect x="0.5" y="3.5" width="6" height="4.5" rx="0.6" fill="#33a6d7"/><path d="M1.7 3.6V2.4a1.8 1.8 0 0 1 3.6 0v1.2" fill="none" stroke="#33a6d7" stroke-width="1"/></svg>
      LOGIN
    </div>
    <div class="abs btn-join">JOIN</div>
  </header>

  <section>
    <div class="abs hero" role="img" aria-label="Founder doing a floor core exercise in a living room"></div>
    <div class="abs hero-shade"></div>
    <p class="abs hero-quote">“Bouncing back is all about getting back to a fitter, healthier , more energetic version of you – something the whole family will benefit from”</p>
    <p class="abs hero-author">- Maren Holloway – Tidewell Mamas Founder</p>
  </section>

  <div class="abs breadcrumb">HOME &nbsp;&gt;&gt;&nbsp; <span class="is-current">ABOUT US</span></div>
  <div class="abs rule"></div>

  <div class="abs founder-photo" role="img" aria-label="Founder smiling while holding her two young daughters"></div>

  <article class="abs story">
    <p>After a life time of competitive sports and as a qualified personal trainer, I thought I knew exactly what it would take to get back into shape after having babies. I put on a massive 30 kgs with my first pregnancy and found myself in a situation for the first time in my life where I had to lose a lot of weight. I thought the answer was just to keep training and eating the way I always did before babies, little did I know this wasn’t the best way at all. I struggled with losing the weight and I also struggled with a lot of back pain and with abdominal separation that wouldn’t fix itself.</p>
    <p>From here i spent a lot of time and energy studying post pregnancy training and found I was doing it all wrong. I totally underestimated the power of core strength and the benefit of easing yourself back into training with the correct post pregnancy specific exercises. I also found my diet was all wrong for someone trying to lose weight with way too much allocation to starchy high GI carbs on my plate and not enough veggies and proteins.</p>
    <p>After my second pregnancy I was so excited to trial out some of my new found knowledge to see how it would go as once again I found myself in a situation of putting on another 25kg. Pleasingly I was able to not only bounce back into shape a lot quicker this time, most importantly I was able to do so without any back pain and my separation also fixed itself within just a few months.</p>
    <p>This is how I came to create the 12 Week Home Workout Program For Mums. I put pen to paper and wrote down all the training routines I used to get back into shape after my second baby. I then tested it out on other mums to make sure it worked for others too and all of the mums I tested on lost at least 18cms across their body doing the program. I also used this exact same program post baby number 3 and at the end of the 12 week program I was fitter and healthier than I had ever been.</p>
    <p>Of course it wasn’t just the exercise that helped, it was also a commitment to a healthy eating plan with portion controlled meals that are full of the right mix of protein, vegetables and healthy carbs. The recipes I have put together as part of this program are on constant rotation in my kitchen, so you will see its possible to eat delicious meals and still lose weight at the same time.</p>
    <p>I firmly believe that you do not need to go on any crazy diets, take any pills or spend hours away from the family sweating it out at the gym to get back into shape after you have babies. All it takes is a bit of commitment to regular, post pregnancy specific exercise and a healthy balanced diet. With this combination you will not only be fitter and healthier than ever, you will also have loads more energy for you and your family and be feeling great within yourself!</p>
  </article>

  <section>
    <div class="abs cta-band" role="img" aria-label="Faded photo of a mum exercising on a living room floor"></div>
    <h2 class="abs cta-title">It’s your turn to take the time to focus on you.</h2>
    <p class="abs cta-sub">Take the first step to being a fitter, healthier more energetic mumma and join my program today!</p>
    <div class="abs btn-cta">GET STARTED NOW</div>
  </section>

  <footer>
    <div class="abs brand footer-brand"><span class="brand-dot"></span>Tidewell Mamas</div>

    <h3 class="abs footer-heading" style="left:226px">Quick Links</h3>
    <ul class="abs quick-links">
      <li><a>Home</a></li>
      <li><a>About Us</a></li>
      <li><a>Program</a></li>
      <li><a>Blog</a></li>
      <li><a>Shop</a></li>
      <li><a>Contact Us</a></li>
    </ul>

    <h3 class="abs footer-heading" style="left:330px">Subscribe</h3>
    <p class="abs subscribe-text">Register your details below and receive tones of free information on fitness and living a healthy lifestyle</p>
    <div class="abs btn-subscribe">SUBSCRIBE</div>

    <h3 class="abs footer-heading" style="left:530px">Stay Connected</h3>
    <div class="abs social" style="top:1064px"><span class="social-mark"></span>Circlet</div>
    <div class="abs social" style="top:1093px"><span class="social-mark"></span>Snapwall</div>

    <div class="abs footer-rule"></div>
    <p class="abs copyright">Copyrights © 2017, Tidewell Mamas. All rights reserved.</p>
  </footer>
</body>
</html>
```